Request for Business Card Design

Hi. My name is Marlene, I am looking for a new business card design for my company, Quarrow Signal Instruments, LLC. I really like the design you did for Tarsel Venture and was hoping you could do something similar using our full logo and our mark. I am also open to any raised texture design using our mark. I have attached our full logo, which would need to be somewhere on the card, as well as the mark in both outline and full form, as well as our brand colors / guide. The card does not have to be white, as long as our logo and mark appear. I actually like darker colored business cards more, but am open to all options. If you are interested in working with me, please let me know. We would also take the business card design into letterhead design if you can do that.

```html
<!DOCTYPE html>
<html lang="en">
<head>
<meta charset="utf-8">
<title>Quarrow Signal Instruments – Business Card</title>
<link rel="stylesheet" href="https://fonts.googleapis.com/css2?family=Open+Sans:wght@400;600;700&display=swap">
<style>
  :root {
    --backdrop: #3a3a3a;
    --card: #141414;
    --card-back: #171717;
    --accent: #1a9fd0;
    --ink-light: #ffffff;
    --ink-soft: #d9d9d9;
    --ink-emboss: #2b2b2b;
    --divider: #1a7fa6;
  }
  * { box-sizing: border-box; margin: 0; padding: 0; }
  html, body {
    width: 1200px; height: 801px; overflow: hidden;
    background: var(--backdrop);
    font-family: "Open Sans", Arial, sans-serif;
  }
  .stage {
    width: 1200px; height: 801px;
    display: flex; align-items: center; justify-content: center; gap: 40px;
  }
  .card {
    position: relative;
    width: 520px; height: 297px;
    background: var(--card);
    border-bottom: 2px solid var(--accent);
    border-left: 2px solid var(--accent);
  }
  .card--back { background: var(--card-back); }

  .brand {
    position: absolute; left: 48px; top: 62px;
    display: flex; align-items: center; gap: 16px;
  }
  .brand__dot {
    width: 52px; height: 52px; border-radius: 50%;
    background: var(--accent);
  }
  .brand__name {
    color: var(--ink-light); font-weight: 700;
    font-size: 30px; line-height: 1; letter-spacing: 2px;
    text-transform: uppercase;
  }
  .brand__name span { display: block; font-size: 11.5px; letter-spacing: 1.2px; margin-top: 6px; }

  .person {
    position: absolute; left: 48px; bottom: 52px;
  }
  .person__name {
    color: var(--accent); font-weight: 700; font-size: 20px;
    letter-spacing: 1px; text-transform: uppercase;
  }
  .person__role { color: var(--ink-soft); font-size: 13px; margin-top: 2px; padding-left: 92px; }

  .divider {
    position: absolute; left: 278px; bottom: 44px;
    width: 1px; height: 66px; background: var(--divider);
  }

  .contact {
    position: absolute; left: 298px; bottom: 48px;
    list-style: none; color: var(--ink-soft); font-size: 13px;
  }
  .contact__item { display: flex; align-items: center; gap: 8px; line-height: 20px; }
  .contact__icon { width: 11px; height: 11px; flex: none; }

  .back-name {
    position: absolute; left: 50%; top: 50%;
    transform: translate(-50%, -50%);
    color: var(--ink-emboss); font-weight: 700; font-size: 26px;
    letter-spacing: 3px; text-transform: uppercase; white-space: nowrap;
  }
</style>
</head>
<body>
<main class="stage">
  <section class="card card--front" aria-label="Card front">
    <div class="brand">
      <div class="brand__dot"></div>
      <div class="brand__name">Quarrow<span>Signal Instruments</span></div>
    </div>

    <div class="person">
      <p class="person__name">Dorian Vaskel</p>
      <p class="person__role">President</p>
    </div>

    <div class="divider"></div>

    <ul class="contact">
      <li class="contact__item">
        <svg class="contact__icon" viewBox="0 0 12 12"><path fill="#1a9fd0" d="M2.5 1l2 2.2-1 1.2c.7 1.5 1.8 2.6 3.3 3.3l1.2-1 2.2 2-1.2 1.8C4.8 10.3 1.7 7.2 .7 2.2z"/></svg>
        555-014-2290
      </li>
      <li class="contact__item">
        <svg class="contact__icon" viewBox="0 0 12 12"><rect x="0.5" y="2" width="11" height="8" fill="#1a9fd0"/><path d="M0.5 2.5L6 6.5l5.5-4" fill="none" stroke="#141414" stroke-width="1"/></svg>
        d.vaskel@quarrow.com
      </li>
      <li class="contact__item">
        <svg class="contact__icon" viewBox="0 0 12 12"><circle cx="6" cy="6" r="5.5" fill="#1a9fd0"/><path d="M0.5 6h11M6 .5c-2 2-2 9 0 11M6 .5c2 2 2 9 0 11" fill="none" stroke="#141414" stroke-width="0.8"/></svg>
        www.quarrow.com
      </li>
    </ul>
  </section>

  <section class="card card--back" aria-label="Card back">
    <p class="back-name">Quarrow</p>
  </section>
</main>
</body>
</html>
```